holloway paving service

Needs to have phone number 0418259730 and email markholloway@brightmail.com.au.
ABN 62318470915
name mark holloway

For all your concreting solutions
Excavation
Exposed & colour concrete
House & shed slabs
Driveways
Landing & steps

Contact Information for Business Card

ph 0418259730
email markholloway@brightmail.com.au.
ABN 62318470915
name mark holloway

```html
<!DOCTYPE html>
<html lang="en">
<head>
<meta charset="UTF-8">
<title>Holloway Paving Service – Business Card</title>
<link rel="stylesheet" href="https://fonts.googleapis.com/css2?family=Lato:wght@400;700&family=Montserrat:wght@500;600&display=swap">
<style>
  :root {
    --bg: #e9e7e4;
    --card: #ffffff;
    --orange: #ee6a24;
    --grey: #5c5c5e;
    --ink: #2b2b2b;
  }
  * { margin: 0; padding: 0; box-sizing: border-box; }
  html, body { width: 1200px; height: 900px; overflow: hidden; }
  body {
    background: var(--bg);
    font-family: "Lato", sans-serif;
    color: var(--ink);
    position: relative;
  }
  .card-shadow {
    position: absolute;
    left: 178px; top: 188px;
    width: 845px; height: 524px;
    filter: drop-shadow(0 14px 28px rgba(0,0,0,0.18));
  }
  .card {
    position: absolute; inset: 0;
    background: var(--card);
    clip-path: polygon(28.5% 0, 100% 0, 100% 100%, 28.5% 100%, 0 50%);
  }
  .contact {
    position: absolute; right: 42px; top: 42px;
    text-align: right;
  }
  .contact__name {
    font-family: "Montserrat", sans-serif;
    font-weight: 600; font-size: 29px; letter-spacing: 0.5px;
    color: var(--grey); text-transform: uppercase;
  }
  .contact__name .first { color: var(--orange); }
  .contact__line { font-size: 22px; margin-top: 14px; color: var(--ink); }
  .contact__line + .contact__line { margin-top: 20px; }

  .brand-mark {
    position: absolute; left: 128px; top: 214px;
    width: 94px; height: 94px;
    background: var(--grey);
  }
  .brand-rule {
    position: absolute; left: 292px; top: 169px;
    width: 3px; height: 186px; background: var(--orange);
  }
  .brand {
    position: absolute; left: 308px; top: 190px; width: 470px;
    text-align: center;
  }
  .brand__name {
    font-family: "Montserrat", sans-serif;
    font-weight: 600; font-size: 34px; line-height: 1.15;
    color: var(--orange); text-transform: uppercase; letter-spacing: 0.5px;
  }
  .brand__sub {
    display: flex; align-items: center; gap: 16px;
  }
  .brand__sub::before, .brand__sub::after {
    content: ""; flex: 1; height: 3px; background: var(--grey);
  }
  .brand__phone {
    font-family: "Montserrat", sans-serif; font-weight: 500;
    font-size: 28px; letter-spacing: 3px; color: var(--orange);
    margin-top: 4px;
  }

  .services {
    position: absolute; right: 42px; top: 366px;
    text-align: right;
  }
  .services__tagline {
    font-weight: 700; font-size: 21px; color: var(--orange);
    text-transform: uppercase; margin-bottom: 14px;
  }
  .services__row { font-size: 23px; line-height: 32px; }
  .sep { color: var(--orange); margin: 0 6px; }
</style>
</head>
<body>
  <div class="card-shadow">
    <div class="card">
      <div class="contact">
        <p class="contact__name"><span class="first">Mark</span> Holloway</p>
        <p class="contact__line">ABN 62318470915</p>
        <p class="contact__line">markholloway@brightmail.com.au</p>
      </div>

      <div class="brand-mark"></div>
      <div class="brand-rule"></div>
      <div class="brand">
        <p class="brand__name">Holloway Paving</p>
        <p class="brand__name brand__sub">Service</p>
        <p class="brand__phone">0418259730</p>
      </div>

      <div class="services">
        <p class="services__tagline">For all your concreting solutions</p>
        <p class="services__row">Excavation<span class="sep">|</span>Exposed &amp; colour concrete</p>
        <p class="services__row">House &amp; shed slabs<span class="sep">|</span>Driveways<span class="sep">|</span>Landing &amp; steps</p>
      </div>
    </div>
  </div>
</body>
</html>
```